Elmhollow Restaurnt Lunch Menu Redesign:

We have two lunch special menus that need to be reformatted into a 4.25inx11in and need a graphics design update. Some menu items need to change and some descriptions need to updated. This new menu should double sided with the Main Dining Lunch Menu on the front side and Teppanyaki Lunch menu on the back.

Both menus should follow the same design formatting as the main dining lunch menu (font, sizing, ect.)

```html
<!DOCTYPE html>
<html lang="en">
<head>
<meta charset="utf-8">
<title>Elmhollow Restaurnt Lunch Menu</title>
<link href="https://fonts.googleapis.com/css2?family=Anton&family=Oswald:wght@400;600&family=Barlow:wght@400;500&family=Dancing+Script:wght@700&display=swap" rel="stylesheet">
<style>
  :root {
    --navy: #0b347e;
    --red: #e0182d;
    --paper: #fbfcfe;
    --rule: #9aabd0;
    --stage: #3a3a3a;
  }
  * { margin: 0; padding: 0; box-sizing: border-box; }
  html, body { width: 1040px; height: 1200px; overflow: hidden; background: var(--stage); }
  .menu-sheet {
    position: absolute; top: 87px; width: 397px; height: 1026px;
    background: var(--paper); overflow: hidden;
    font-family: "Barlow", Arial, sans-serif; color: var(--navy);
  }
  .front { left: 84px; }
  .back { left: 559px; }
  .ornament { position: absolute; background: var(--navy); border-radius: 48% 52% 45% 50%; z-index: 0; }
  .menu-sheet > :not(.ornament) { z-index: 1; }
  .display { position: absolute; left: 0; top: 0; overflow: visible; }
  .script {
    position: absolute; font-family: "Dancing Script", cursive; font-weight: 700; color: var(--red);
    white-space: nowrap; line-height: 1; transform: translate(-50%, -50%) rotate(-6deg);
    paint-order: stroke fill; -webkit-text-stroke: 4px var(--paper);
  }
  .hours-box {
    position: absolute; border: 1px solid var(--rule);
    display: flex; align-items: center; justify-content: center; white-space: nowrap;
    font-family: "Oswald", sans-serif; font-weight: 400; font-size: 24px;
    text-transform: uppercase; color: var(--navy);
  }
  .hours-box strong { color: var(--red); font-weight: 600; margin-left: 7px; }
  .hours-box.ages { font-size: 17px; letter-spacing: 0; }
  .section-frame { position: absolute; left: 40px; width: 318px; border: 1px solid var(--rule); }
  .section-frame.double { outline: 1px solid var(--rule); outline-offset: -4px; }
  .section-title {
    position: absolute; left: 57px; height: 30px; line-height: 30px;
    font-family: "Oswald", sans-serif; font-weight: 600; font-size: 27px;
    text-transform: uppercase; color: var(--navy);
    background: var(--paper); padding-right: 8px;
  }
  .note { position: absolute; left: 57px; width: 290px; font-size: 11.2px; line-height: 14.5px; }
  .note b { color: var(--red); font-weight: 500; }
  .note.center { left: 0; width: 397px; text-align: center; }
  .item {
    position: absolute; left: 57px; width: 280px; height: 16px;
    display: flex; align-items: flex-end; font-size: 13px; line-height: 16px;
  }
  .back .item { left: 56px; }
  .item .name { color: var(--red); white-space: nowrap; }
  .item .rule { flex: 1; border-bottom: 1px solid var(--rule); margin: 0 6px 4px; }
  .item .price { color: var(--red); width: 22px; white-space: nowrap; }
  .item .price sup { font-size: 7px; vertical-align: 6px; }
  .desc { position: absolute; left: 58px; font-size: 8px; line-height: 10px; color: var(--navy); }
  .sushi-line { position: absolute; left: 57px; font-size: 12.5px; line-height: 16px; color: var(--red); white-space: nowrap; }
  .sushi-line small { font-size: 8px; color: var(--navy); margin-right: 6px; }
  .sushi-divider { position: absolute; left: 57px; width: 290px; border-top: 1px solid var(--rule); }
  .sushi-pipe { position: absolute; left: 173px; width: 0; height: 26px; border-left: 1px solid var(--rule); }
  .raw-footer { position: absolute; left: 0; width: 397px; text-align: center; }
  .raw-title {
    top: 953px; font-family: "Oswald", sans-serif; font-weight: 600; font-size: 15px;
    text-transform: uppercase; display: flex; justify-content: center; align-items: center; gap: 8px;
  }
  .raw-title::before, .raw-title::after { content: ""; width: 52px; border-top: 1px solid var(--navy); }
  .raw-gratuity { top: 968px; font-size: 12px; }
  .raw-gratuity b { color: var(--red); font-weight: 500; }
  .raw-warning { top: 985px; font-size: 8px; }
</style>
</head>
<body>

<section class="menu-sheet front" aria-label="Elmhollow Restaurnt main dining lunch specials">
  <div class="ornament" role="img" aria-label="Decorative swirling cloud" style="left:338px; top:200px; width:59px; height:36px;"></div>
  <div class="ornament" role="img" aria-label="Decorative ocean wave" style="left:0; top:400px; width:50px; height:24px;"></div>
  <div class="ornament" role="img" aria-label="Decorative swirling cloud" style="left:345px; top:570px; width:52px; height:56px;"></div>
  <div class="ornament" role="img" aria-label="Decorative ocean wave" style="left:0; top:940px; width:40px; height:36px;"></div>

  <svg class="display" width="397" height="160" aria-hidden="true">
    <text x="37" y="141" font-family="Anton, sans-serif" font-size="156" fill="#0b347e" textLength="323" lengthAdjust="spacingAndGlyphs">LUNCH</text>
  </svg>
  <div class="script" style="left:198px; top:86px; font-size:52px;">Specials</div>
  <div class="hours-box" style="left:53px; top:155px; width:291px; height:39px;">Served Daily<strong>11AM - 3PM</strong></div>

  <div class="section-frame" style="top:225px; height:183px;"></div>
  <h2 class="section-title" style="top:211px;">Sandwiches</h2>
  <p class="note" style="top:240px;">Served with Choice of Miso Soup or House Salad &amp; Potato Chips</p>
  <div class="item" style="top:274px;"><span class="name">Fried Breaded Calamari Steak</span><span class="rule"></span><span class="price"><sup>$</sup>16</span></div>
  <p class="desc" style="top:291px;">with Tomato, Lettuce &amp; Onion</p>
  <div class="item" style="top:307px;"><span class="name">Grilled Chicken</span><span class="rule"></span><span class="price"><sup>$</sup>16</span></div>
  <p class="desc" style="top:325px;">with Bacon, Tomato, Lettuce &amp; Mayonnaise Drizzle</p>
  <div class="item" style="top:336px;"><span class="name">Hamburger</span><span class="rule"></span><span class="price"><sup>$</sup>18</span></div>
  <p class="desc" style="top:355px;">with Lettuce, Tomato, Onion, Mayonnaise Drizzle</p>
  <div class="item" style="top:370px;"><span class="name">Fried Soft Shell Crab Burger</span><span class="rule"></span><span class="price"><sup>$</sup>20</span></div>
  <p class="desc" style="top:387px;">with Avocado, Lettuce, Tomato, Onion &amp; Mayo</p>

  <div class="section-frame" style="top:439px; height:151px;"></div>
  <h2 class="section-title" style="top:424px;">Sushi Specials</h2>
  <p class="note" style="top:453px;">Please Select 4 of the followings for <b>$ 16</b><br>Served with a 4 piece California Roll &amp; Miso Soup or House Salad</p>
  <p class="sushi-line" style="top:501px;">Hamachi <small>Yellowtail Tuna</small>Hotate <small>Scallop</small>Ika <small>Squid</small></p>
  <p class="sushi-line" style="top:517px;">Ikura <small>Salmon Roe</small>Saba <small>Mackerel</small>Sake <small>Salmon</small>Tai <small>Red Snapper</small></p>
  <div class="sushi-divider" style="top:540px;"></div>
  <p class="sushi-line" style="top:546px;">Maguro <small>Yellow fin Tuna</small></p>
  <p class="sushi-line" style="top:564px;">Smoked Salmon</p>
  <div class="sushi-pipe" style="top:550px;"></div>
  <p class="sushi-line" style="top:546px; left:187px;">Tako <small>Octopus</small>Ebi <small>Shrimp</small></p>
  <p class="sushi-line" style="top:564px; left:187px;">Unagi <small>BBQ Eel</small>Tamago <small>Egg</small></p>

  <div class="section-frame" style="top:622px; height:321px;"></div>
  <h2 class="section-title" style="top:606px;">Main Courses</h2>
  <p class="note" style="top:637px;">Served with Rice &amp; Choice of Miso Soup or House Salad<br>All Meals Served with Rice. Upgrade to fried rice<br>for only <b>$4</b></p>
  <div class="item" style="top:684px;"><span class="name">Organic Tofu Teriyaki</span><span class="rule"></span><span class="price"><sup>$</sup>14</span></div>
  <p class="desc" style="top:701px;">Served Grilled or Tempura Fried</p>
  <div class="item" style="top:718px;"><span class="name">Chicken Teriyaki</span><span class="rule"></span><span class="price"><sup>$</sup>16</span></div>
  <div class="item" style="top:743px;"><span class="name">Spicy Chicken Teriyaki</span><span class="rule"></span><span class="price"><sup>$</sup>16</span></div>
  <div class="item" style="top:768px;"><span class="name">Beef Teriyaki</span><span class="rule"></span><span class="price"><sup>$</sup>16</span></div>
  <div class="item" style="top:791px;"><span class="name">Spicy Beef Teriyaki</span><span class="rule"></span><span class="price"><sup>$</sup>16</span></div>
  <div class="item" style="top:817px;"><span class="name">Chicken Katsu</span><span class="rule"></span><span class="price"><sup>$</sup>15</span></div>
  <p class="desc" style="top:834px;">Breaded Chicken Breast</p>
  <div class="item" style="top:849px;"><span class="name">Katsu Don</span><span class="rule"></span><span class="price"><sup>$</sup>16</span></div>
  <p class="desc" style="top:865px;">Fried Chicken Breast, Egg &amp; Onion over Rice</p>
  <div class="item" style="top:880px;"><span class="name">Unagi Don</span><span class="rule"></span><span class="price"><sup>$</sup>19</span></div>
  <p class="desc" style="top:897px;">BBQ Eel over Rice</p>
  <div class="item" style="top:912px;"><span class="name">Shrimp &amp; Vegetable Tempura</span><span class="rule"></span><span class="price"><sup>$</sup>16</span></div>

  <p class="raw-footer raw-title">Served Raw</p>
  <p class="raw-footer raw-gratuity"><b>20%</b> gratuity added to parties of <b>6</b> or more.</p>
  <p class="raw-footer raw-warning">Consuming raw or undercooked food may increase your risk of foodborne illness</p>
</section>

<section class="menu-sheet back" aria-label="Elmhollow Restaurnt teppanyaki lunch">
  <div class="ornament" role="img" aria-label="Decorative swirling cloud" style="left:0; top:95px; width:48px; height:40px;"></div>
  <div class="ornament" role="img" aria-label="Decorative swirling cloud" style="left:350px; top:130px; width:47px; height:36px;"></div>
  <div class="ornament" role="img" aria-label="Decorative swirling cloud" style="left:0; top:672px; width:56px; height:40px;"></div>
  <div class="ornament" role="img" aria-label="Decorative ocean wave" style="left:330px; top:690px; width:67px; height:36px;"></div>
  <div class="ornament" role="img" aria-label="Decorative ocean wave" style="left:0; top:975px; width:48px; height:46px;"></div>

  <svg class="display" width="397" height="720" aria-hidden="true">
    <text x="38" y="87" font-family="Anton, sans-serif" font-size="78" fill="#0b347e" textLength="321" lengthAdjust="spacingAndGlyphs">TEPPANYAKI</text>
    <text x="92" y="696" font-family="Anton, sans-serif" font-size="72" fill="#0b347e" textLength="211" lengthAdjust="spacingAndGlyphs">SPECIAL</text>
  </svg>
  <div class="script" style="left:198px; top:95px; font-size:52px;">Lunch</div>
  <div class="hours-box" style="left:53px; top:126px; width:290px; height:40px;">Available Until<strong>11-2:30PM</strong></div>
  <p class="note center" style="top:171px;">Served with Miso Soup or Salad, Choice of Rice &amp; Vegetables</p>

  <div class="section-frame double" style="left:39px; top:204px; width:319px; height:410px;"></div>
  <div class="item" style="top:217px;"><span class="name">Hibachi Chicken</span><span class="rule"></span><span class="price"><sup>$</sup>18</span></div>
  <div class="item" style="top:243px;"><span class="name">Hibachi Shrimp</span><span class="rule"></span><span class="price"><sup>$</sup>19</span></div>
  <div class="item" style="top:269px;"><span class="name">Hibachi New York Steak</span><span class="rule"></span><span class="price"><sup>$</sup>20</span></div>
  <div class="item" style="top:295px;"><span class="name">Hibachi Salmon</span><span class="rule"></span><span class="price"><sup>$</sup>20</span></div>
  <div class="item" style="top:320px;"><span class="name">Teriyaki Beef</span><span class="rule"></span><span class="price"><sup>$</sup>19</span></div>
  <div class="item" style="top:347px;"><span class="name">Hibachi Scallop</span><span class="rule"></span><span class="price"><sup>$</sup>20</span></div>
  <div class="item" style="top:372px;"><span class="name">Chicken and Shrimp</span><span class="rule"></span><span class="price"><sup>$</sup>21</span></div>
  <div class="item" style="top:398px;"><span class="name">Scallop and Shrimp</span><span class="rule"></span><span class="price"><sup>$</sup>22</span></div>
  <div class="item" style="top:424px;"><span class="name">New York Steak and Chicken</span><span class="rule"></span><span class="price"><sup>$</sup>22</span></div>
  <div class="item" style="top:450px;"><span class="name">New York Steak and Shrimp</span><span class="rule"></span><span class="price"><sup>$</sup>23</span></div>
  <div class="item" style="top:477px;"><span class="name">New York Steak and Scallop</span><span class="rule"></span><span class="price"><sup>$</sup>24</span></div>
  <div class="item" style="top:502px;"><span class="name">Filet Mignon</span><span class="rule"></span><span class="price"><sup>$</sup>23</span></div>
  <div class="item" style="top:528px;"><span class="name">Filet Mignon and Chicken</span><span class="rule"></span><span class="price"><sup>$</sup>25</span></div>
  <div class="item" style="top:554px;"><span class="name">Filet Mignon and Shrimp</span><span class="rule"></span><span class="price"><sup>$</sup>26</span></div>
  <div class="item" style="top:580px;"><span class="name">Filet Mignon and Scallop</span><span class="rule"></span><span class="price"><sup>$</sup>27</span></div>

  <div class="script" style="left:200px; top:712px; font-size:56px;">Menu</div>
  <div class="hours-box ages" style="left:38px; top:740px; width:320px; height:32px;">Ages 12 and under ~ Ages 65 and older</div>
  <p class="note center" style="top:781px;">Served with Miso Soup or Salad, Choice of Rice &amp; Vegetables</p>

  <div class="section-frame double" style="left:39px; top:816px; width:319px; height:172px;"></div>
  <div class="item" style="top:831px;"><span class="name">Hibachi Chicken</span><span class="rule"></span><span class="price"><sup>$</sup>15</span></div>
  <div class="item" style="top:856px;"><span class="name">Hibachi Shrimp</span><span class="rule"></span><span class="price"><sup>$</sup>16</span></div>
  <div class="item" style="top:881px;"><span class="name">Hibachi Scallop</span><span class="rule"></span><span class="price"><sup>$</sup>18</span></div>
  <div class="item" style="top:906px;"><span class="name">Hibachi New York Steak</span><span class="rule"></span><span class="price"><sup>$</sup>18</span></div>
  <div class="item" style="top:930px;"><span class="name">Hibachi Scallop</span><span class="rule"></span><span class="price"><sup>$</sup>18</span></div>
  <div class="item" style="top:955px;"><span class="name">Teriyaki Beef</span><span class="rule"></span><span class="price"><sup>$</sup>16</span></div>
</section>

</body>
</html>
```